Fenwick Grading LTD - website for irrigation & Landscape Lighting & Buried service wire

Looking for a website to help promote my business with Irrigation (installation, service, etc) and buried service wire/drainage solutions.

Commercial/Residential

Landscape lighting.

I’ll get photos in the trucks and trailers to upload as well maybe the machine as well.

Target Market(s)

Homeowners who want green grass and beautiful gardens. Beautiful landscape lighting

Industry/Entity Type

Irrigation systems and landscape lighting and buried service wire to homes and offering Drainage soltions.

Coding

Coded - Design and coding required

Number of Pages Required

4 page

Colors
F0912C
F2A743
F7CA91
FBE8D2
FDF5EE

Requirements
Must have
• was hoping to link up my email on fenwickgrading@mailbox-example.net with the website if possible.
Nice to have
• Page for Irrigation, page for landscape lighting, page buried service wire & drainage soltions.

```html
<!DOCTYPE html>
<html lang="en">
<head>
<meta charset="UTF-8">
<title>Fenwick Grading LTD</title>
<link href="https://fonts.googleapis.com/css2?family=Roboto:wght@400;500;700&display=swap" rel="stylesheet">
<style>
:root{
  --orange:#F0912C;
  --orange-2:#F2A743;
  --orange-3:#F7CA91;
  --orange-4:#FBE8D2;
  --cream:#FDF5EE;
  --ink:#111111;
  --text:#3a3a3a;
  --band:#808080;
  --footer:#000000;
  --white:#ffffff;
}
*{margin:0;padding:0;box-sizing:border-box}
html,body{width:1200px;height:3387px;overflow:hidden}
body{font-family:'Roboto',sans-serif;color:var(--text);background:var(--white);position:relative}
a{color:inherit;text-decoration:none}

/* header */
.site-header{position:absolute;top:0;left:0;width:1200px;height:84px;background:var(--white);display:flex;align-items:center}
.brand{position:absolute;left:138px;top:27px;display:flex;align-items:center;gap:8px;font-weight:500;font-size:18px;color:var(--orange)}
.brand-square{width:14px;height:14px;background:var(--orange)}
.main-nav{position:absolute;right:112px;top:31px;display:flex;gap:23px;font-size:15.5px;color:var(--ink)}

/* hero */
.hero{position:absolute;top:84px;left:0;width:1200px;height:600px;
  background:radial-gradient(ellipse at 50% 20%,#7b7a5a 0%,#4d5b2c 35%,transparent 70%),linear-gradient(180deg,#6a6a58 0%,#4f6230 35%,#4a7a22 60%,#3c6a1a 100%);text-align:center;color:var(--white)}
.hero-welcome{position:absolute;top:170px;width:100%;font-size:50px;font-weight:400}
.hero-title{position:absolute;top:240px;width:100%;font-size:98px;font-weight:700;letter-spacing:-0.5px;line-height:1.1}
.hero-btn{position:absolute;top:379px;left:534px;width:131px;height:42px;background:var(--white);color:var(--orange);border-radius:3px;font-size:15px;line-height:42px}

/* about */
.about-photo{position:absolute;top:770px;left:112px;width:427px;height:513px;border-radius:4px;background:radial-gradient(circle at 50% 70%,#b08a6a 0%,#6a5a40 20%,transparent 45%),linear-gradient(180deg,#1d2a22 0%,#23402a 45%,#2f5a22 100%)}
.about-copy{position:absolute;top:790px;left:628px;width:460px}
.about-copy h2{font-size:40px;font-weight:700;color:var(--ink);margin-bottom:22px}
.about-copy p{font-size:15.5px;line-height:25.7px;margin-bottom:17px}
.btn-orange{display:inline-block;background:var(--orange);color:var(--white);border-radius:3px;font-size:15px;text-align:center}
.about-copy .btn-orange{width:132px;height:42px;line-height:42px;margin-top:16px}

/* section heads */
.section-head{position:absolute;left:0;width:1200px;text-align:center}
.section-head h2{font-size:40px;font-weight:700;color:var(--ink)}
.section-head p{font-size:15px;line-height:22.5px;margin:14px auto 0}

/* cards */
.card-row{position:absolute;left:112px;display:flex;gap:27px}
.card{width:307px}
.card-photo{width:307px;height:251px}
.card h3{font-size:25px;font-weight:700;color:var(--orange);line-height:26px;margin-top:22px}
.card p{font-size:15px;line-height:22.5px;margin-top:11px;width:250px}
.card .more{display:inline-block;margin-top:8px;font-size:15px;font-weight:700;color:var(--ink);text-decoration:underline;padding-left:2px}
.blog .card h3{font-size:21px;margin-top:23px}
.blog .card p{width:270px;margin-top:14px}

.dots{position:absolute;top:1977px;left:570px;display:flex;gap:13px;align-items:center}
.dot{width:10px;height:10px;border-radius:50%;background:#8a8a8a}
.dot.active{width:14px;height:14px;background:var(--orange)}

/* newsletter band */
.newsletter-band{position:absolute;top:2081px;left:0;width:1200px;height:184px;background:var(--band)}
.newsletter-title{position:absolute;left:113px;top:70px;display:flex;align-items:center;gap:14px;color:var(--white);font-size:30px;font-weight:700}
.subscribe-form{position:absolute;left:636px;top:63px;width:452px;height:60px;background:var(--white);border-radius:4px}
.subscribe-form span{position:absolute;left:16px;top:23px;font-size:10.5px;color:var(--ink)}
.subscribe-form .btn-orange{position:absolute;right:8px;top:8px;width:124px;height:43px;line-height:43px;font-size:16px}

/* footer */
.site-footer{position:absolute;top:3012px;left:0;width:1200px;height:375px;background:var(--footer);color:var(--white)}
.footer-brand{position:absolute;left:112px;top:108px;display:flex;align-items:center;gap:8px;font-size:19px;font-weight:500}
.footer-brand .brand-square{background:var(--white)}
.footer-col{position:absolute;top:68px}
.footer-col h4{font-size:19px;font-weight:700;margin-bottom:16px}
.address{left:352px}
.address h4{margin-left:28px}
.contact-line{display:flex;gap:10px;font-size:13.5px;line-height:22px;margin-bottom:5px;width:230px}
.contact-line svg{flex:none;margin-top:4px}
.links{left:640px}
.links ul{list-style:none;font-size:15px;line-height:25.8px}
.foot-news{left:850px;width:237px}
.foot-news .field{display:flex;align-items:center;gap:8px;border-bottom:1px solid var(--white);padding-bottom:9px;font-size:8px}
.foot-news .field svg:last-child{margin-left:auto}
.socials{display:flex;gap:21px;margin-top:28px}
.socials span{width:22px;height:22px;background:var(--white);border-radius:2px}
.footer-rule{position:absolute;left:0;top:334px;width:1200px;height:1px;background:#555}
.copyright{position:absolute;top:349px;width:1200px;text-align:center;font-size:13px}
</style>
</head>
<body>

<header class="site-header">
  <a class="brand" href="#"><span class="brand-square"></span>Fenwick Grading LTD</a>
  <nav class="main-nav">
    <a href="#">Home</a><a href="#">About Us</a><a href="#">Irrigation</a><a href="#">Services</a><a href="#">Landscape Lighting</a><a href="#">Fiber Optic Installation</a><a href="#">Contact Us</a>
  </nav>
</header>

<section class="hero" role="img" aria-label="Sprinkler watering a green lawn in front of a house">
  <div class="hero-welcome">Welcome to</div>
  <h1 class="hero-title">Fenwick Grading</h1>
  <a class="hero-btn" href="#">Contact Us</a>
</section>

<section class="about">
  <div class="about-photo" role="img" aria-label="Stone garden path lit by landscape lights at night"></div>
  <div class="about-copy">
    <h2>About Us</h2>
    <p>Lorem ipsum dolor sit amet, consectetur adipiscing elit, sed do eiusmod tempor incididunt ut labore et dolore magna aliqua. Ut enim ad minim veniam, quis nostrud exercitation ullamco laboris nisi ut aliquip ex ea commodo consequat. Duis aute irure dolor in reprehenderit in voluptate velit esse cillum dolore eu fugiat nulla pariatur.</p>
    <p>Sed ut perspiciatis unde omnis iste natus error sit voluptatem accusantium doloremque laudantium, totam rem aperiam, eaque ipsa quae ab illo inventore veritatis et quasi architecto beatae vitae dicta sunt explicabo. Nemo enim ipsam voluptatem quia voluptas sit aspernatur aut odit aut fugit, sed quia consequuntur magni dolores eos qui ratione voluptatem sequi nesciunt.</p>
    <a class="btn-orange" href="#">Read More</a>
  </div>
</section>

<div class="section-head" style="top:1362px">
  <h2>Our Services</h2>
  <p style="width:830px">Duis aute irure dolor in reprehenderit in voluptate velit esse cillum dolore eu fugiat nulla pariatur. Excepteur sint occaecat cupidatat non proident, sunt in culpa qui officia deserunt mollit anim id est laborum.</p>
</div>

<div class="card-row services" style="top:1506px">
  <article class="card">
    <div class="card-photo" role="img" aria-label="Technician installing irrigation parts in a garden" style="background:linear-gradient(135deg,#6b8a3a 0%,#3e7a3a 45%,#2a6a40 70%,#9a8a70 100%)"></div>
    <h3>Irrigation Installs</h3>
    <p>Excepteur sint occaecat cupidatat non proident, sunt in culpa qui officia deserunt mollit anim id est laborum.</p>
    <a class="more" href="#">Read More....</a>
  </article>
  <article class="card">
    <div class="card-photo" role="img" aria-label="House at dusk with landscape lighting" style="background:radial-gradient(circle at 45% 65%,#b07a40 0%,transparent 30%),linear-gradient(180deg,#3a3f6e 0%,#2c3466 55%,#1e2a30 100%)"></div>
    <h3>Landscape Lighting</h3>
    <p>Excepteur sint occaecat cupidatat non proident, sunt in culpa qui officia deserunt mollit anim id est laborum.</p>
    <a class="more" href="#">Read More....</a>
  </article>
  <article class="card">
    <div class="card-photo" role="img" aria-label="Hand plugging yellow fiber optic cables into a network unit" style="background:radial-gradient(circle at 65% 55%,#c9a630 0%,transparent 25%),linear-gradient(135deg,#5a6470 0%,#9aa2ac 45%,#c8ccd2 100%)"></div>
    <h3>Fiber Optic Installation</h3>
    <p>Excepteur sint occaecat cupidatat non proident, sunt in culpa qui officia deserunt mollit anim id est laborum.</p>
    <a class="more" href="#">Read More....</a>
  </article>
</div>

<div class="dots"><span class="dot"></span><span class="dot active"></span><span class="dot"></span></div>

<section class="newsletter-band">
  <div class="newsletter-title">
    <svg width="40" height="40" viewBox="0 0 40 40" fill="none" stroke="#fff" stroke-width="2"><path d="M4 16 L20 5 L36 16 V36 H4 Z"/><path d="M4 16 L20 27 L36 16"/><path d="M4 36 L16 25 M36 36 L24 25"/><rect x="10" y="9" width="20" height="12"/></svg>
    Subscribe to our Newsletter
  </div>
  <form class="subscribe-form">
    <span>Your Email Address...</span>
    <a class="btn-orange" href="#">Submit</a>
  </form>
</section>

<div class="section-head" style="top:2344px">
  <h2>Our Blog</h2>
  <p style="width:570px">Lorem ipsum dolor sit amet, consectetur adipiscing elit, sed do eiusmod tempor incididunt ut labore et dolore magna aliqua.</p>
</div>

<div class="card-row blog" style="top:2498px">
  <article class="card">
    <div class="card-photo" role="img" aria-label="Trench with buried service cables in soil" style="background:linear-gradient(135deg,#7a7066 0%,#5e564c 40%,#8a8070 60%,#6a7a5a 100%)"></div>
    <h3>Excepteur sint occaecat&nbsp; non proident</h3>
    <p>Excepteur sint occaecat cupidatat non proident, sunt in culpa qui officia deserunt mollit anim id est laborum.</p>
    <a class="more" href="#">Read More</a>
  </article>
  <article class="card">
    <div class="card-photo" role="img" aria-label="Sprinkler head spraying water over grass" style="background:linear-gradient(180deg,#3a4a2a 0%,#5a7a3a 45%,#6aa02a 75%,#4a3a2a 100%)"></div>
    <h3>Duis aute irure dolor in reprehenderit</h3>
    <p>Duis aute irure dolor in reprehenderit in voluptate velit esse cillum dolore eu fugiat nulla pariatur.</p>
    <a class="more" href="#">Read More</a>
  </article>
  <article class="card">
    <div class="card-photo" role="img" aria-label="Lit house and garden bridge at night" style="background:radial-gradient(circle at 55% 70%,#c08a40 0%,transparent 35%),linear-gradient(180deg,#1e2c3a 0%,#2a3a2a 50%,#3a3020 100%)"></div>
    <h3>Sed ut perspiciatis unde omnis iste</h3>
    <p>Sed ut perspiciatis unde omnis iste natus error sit voluptatem accusantium doloremque laudantium,</p>
    <a class="more" href="#">Read More</a>
  </article>
</div>

<footer class="site-footer">
  <div class="footer-brand"><span class="brand-square"></span>Fenwick Grading LTD</div>

  <div class="footer-col address">
    <h4>Address</h4>
    <div class="contact-line">
      <svg width="14" height="14" viewBox="0 0 24 24" fill="#fff"><path d="M6.6 10.8a15 15 0 0 0 6.6 6.6l2.2-2.2c.3-.3.7-.4 1-.2 1.1.4 2.3.6 3.6.6.6 0 1 .4 1 1V20c0 .6-.4 1-1 1A17 17 0 0 1 3 4c0-.6.4-1 1-1h3.5c.6 0 1 .4 1 1 0 1.3.2 2.5.6 3.6.1.3 0 .7-.2 1z"/></svg>
      <span>+ 1 555 014 2290</span>
    </div>
    <div class="contact-line">
      <svg width="14" height="12" viewBox="0 0 24 18" fill="none" stroke="#fff" stroke-width="2"><rect x="1" y="1" width="22" height="16"/><path d="M1 1l11 9 11-9"/></svg>
      <span>fenwickgrading@mailbox-example.net</span>
    </div>
    <div class="contact-line" style="margin-top:14px">
      <svg width="14" height="16" viewBox="0 0 24 28" fill="none" stroke="#fff" stroke-width="2.5"><path d="M12 26s9-9 9-15a9 9 0 0 0-18 0c0 6 9 15 9 15z"/><circle cx="12" cy="11" r="3.5"/></svg>
      <span>123, Fenwick Grading Lorem ipsum dolor sit amet.</span>
    </div>
  </div>

  <div class="footer-col links">
    <h4>Links</h4>
    <ul>
      <li>Home</li><li>About Us</li><li>Irrigation</li><li>Services</li><li>Landscape Lighting</li><li>Fiber Optic Installation</li><li>Contact Us</li>
    </ul>
  </div>

  <div class="footer-col foot-news">
    <h4>Newsletter</h4>
    <div class="field">
      <svg width="14" height="10" viewBox="0 0 24 18" fill="none" stroke="#fff" stroke-width="2"><rect x="1" y="1" width="22" height="16"/><path d="M1 1l11 9 11-9"/></svg>
      <span>Enter Your Email Id</span>
      <svg width="22" height="12" viewBox="0 0 22 12" fill="none" stroke="#fff" stroke-width="1.5"><path d="M0 6h20M15 1l5 5-5 5"/></svg>
    </div>
    <div class="socials"><span></span><span></span><span></span></div>
  </div>

  <div class="footer-rule"></div>
  <div class="copyright">© 2024 Fenwick Grading</div>
</footer>

</body>
</html>
```